card for handyman and landscaping business, double sided with services listed on the back

Design a business card for a handyman and Landscaping business in San Jose,ca. Would like front to be a house with 3D characters doing different tasks i.e. Mowing lawn, painting, sprinklers, lighting, weed whacking, power washing, lumber etc. on the backside a cutout of the interior with computer, internet, cleaning, bathroom/kitchen remodeling, smart home etc.

Industry/Entity Type

Handyman

Contact Information for Business Card

Two sided view of a house, one outside services and one inside services

Colors

Designer to choose colors to be used in the design.

Requirements
Must have
• General Household Repairs and Maintenance
• Landscaping, Gardening, and Planting
• Painting, Patching and Trim/Moulding Work
• Cleaning, Restoring and Hauling/Trash Removal
• Blinds, Curtains, and Assembly Work
• Computer, Internet/Wireless, and Smart Home Service

```html
<!DOCTYPE html>
<html lang="en">
<head>
<meta charset="utf-8">
<title>Handyman, Landscaping and Tech Services – Business Card</title>
<link href="https://fonts.googleapis.com/css2?family=Source+Sans+3:wght@400;600;700&display=swap" rel="stylesheet">
<style>
  :root{
    --stage:#545454;
    --card-dark:#1b1b1b;
    --card-dark-back:#121212;
    --green:#2e8b14;
    --green-bright:#39a51b;
    --band:#efefef;
    --white:#ffffff;
  }
  *{box-sizing:border-box;margin:0;padding:0}
  html,body{width:1200px;height:900px;overflow:hidden;background:var(--stage)}
  body{position:relative;font-family:"Source Sans 3",Arial,sans-serif;color:var(--white)}
  .card{position:absolute;top:306px;width:440px;height:271px;box-shadow:3px 4px 8px rgba(0,0,0,.45);overflow:hidden}
  .card--front{left:149px}
  .card--back{left:608px}
  .card__art{position:absolute;inset:0;width:440px;height:271px;display:block}
  .card__title{position:absolute;top:27px;left:0;width:440px;text-align:center;color:var(--green-bright);font-weight:700;font-size:16.5px;letter-spacing:.1px}
  .contact{position:absolute;left:24px;font-size:13px;line-height:15px;display:flex;align-items:center;gap:6px}
  .contact svg{width:9px;height:9px;fill:var(--green-bright)}
  .contact--phone{top:63px}
  .contact--email{top:79px}
  .address{position:absolute;left:24px;top:104px;font-size:13px;line-height:15px}
  .person{position:absolute;right:24px;top:64px;text-align:right}
  .person__name{color:var(--green-bright);font-weight:700;font-size:15.5px;line-height:17px}
  .person__role{font-size:13px;line-height:15px}
  .website{position:absolute;left:0;top:247px;width:440px;text-align:center;font-size:12.5px}
  .services{position:absolute;top:17px;list-style:none;font-size:11.2px;line-height:14px}
  .services li{position:relative;padding-left:10px}
  .services li::before{content:"";position:absolute;left:0;top:5px;width:4px;height:4px;border-radius:50%;background:var(--green-bright)}
  .services--left{left:16px}
  .services--right{left:268px}
</style>
</head>
<body>

<svg width="0" height="0" style="position:absolute" aria-hidden="true">
  <defs>
    <g id="house-shape">
      <path d="M0 168 H154 L216 137 L266 168 V145 H306 V168 H440 V271 H0 Z" fill="var(--band)"/>
      <path d="M0 168 H154 L216 137 L266 168" fill="none" stroke="var(--green)" stroke-width="4"/>
      <path d="M266 145 H306" stroke="var(--green)" stroke-width="4"/>
      <path d="M306 168 H440" stroke="var(--green)" stroke-width="4"/>
      <rect x="0" y="243" width="440" height="28" fill="var(--green)"/>
    </g>
  </defs>
</svg>

<section class="card card--front">
  <svg class="card__art" viewBox="0 0 440 271" aria-hidden="true">
    <rect width="440" height="271" fill="var(--card-dark)"/>
    <use href="#house-shape"/>
    <g fill="var(--green)">
      <circle cx="56" cy="209" r="25"/><circle cx="121" cy="209" r="25"/><circle cx="187" cy="209" r="25"/>
      <circle cx="252" cy="209" r="25"/><circle cx="318" cy="209" r="25"/><circle cx="384" cy="209" r="25"/>
    </g>
    <g fill="#fff" stroke="#fff">
      <!-- toilet -->
      <rect x="48" y="193" width="14" height="12" rx="1" stroke="none"/>
      <path d="M46 207 H66 Q66 217 58 219 V225 H50 V219 Q46 216 46 207 Z" stroke="none"/>
      <!-- broom -->
      <path d="M132 194 L121 210" stroke-width="2.5" fill="none"/>
      <path d="M116 207 L126 214 L120 224 Q112 222 108 217 Z" stroke="none"/>
      <!-- computer -->
      <rect x="175" y="196" width="24" height="16" rx="1" stroke="none"/>
      <rect x="176" y="216" width="22" height="7" rx="1" stroke="none"/>
      <!-- wifi antenna -->
      <path d="M249 203 L252 198 L255 203 L257 222 H247 Z" stroke="none"/>
      <path d="M243 200 Q239 208 243 216 M261 200 Q265 208 261 216 M238 196 Q232 208 238 220 M266 196 Q272 208 266 220" fill="none" stroke-width="2"/>
      <!-- bulb -->
      <circle cx="318" cy="205" r="8" stroke="none"/>
      <rect x="314" y="213" width="8" height="7" stroke="none"/>
      <path d="M318 190 V193 M305 205 H308 M328 205 H331 M309 196 L311 198 M327 196 L325 198" stroke-width="2" fill="none"/>
      <!-- smart home -->
      <path d="M370 208 L384 195 L398 208 V224 H370 Z" stroke="none"/>
      <circle cx="384" cy="213" r="5" fill="none" stroke="var(--green)" stroke-width="2"/>
      <path d="M384 206 V212" stroke="var(--green)" stroke-width="2"/>
    </g>
  </svg>
  <h1 class="card__title">HANDYMAN , LANDSCAPING AND TECH SERVICES</h1>
  <div class="contact contact--phone"><svg viewBox="0 0 10 10"><path d="M2 0 L4 2 L3 3.5 Q4.5 6 6.5 7 L8 6 L10 8 L8.5 10 Q1 8 0 1.5 Z"/></svg>(044)555019283</div>
  <div class="contact contact--email"><svg viewBox="0 0 10 10"><path d="M0 2 H10 V8 H0 Z M0 2 L5 5.5 L10 2" /></svg>hello@reedhomeworks.com</div>
  <p class="address">1234, Address GoesHere,<br>Country name, 12345</p>
  <div class="person">
    <p class="person__name">MARCUS REED</p>
    <p class="person__role">Managing Director</p>
  </div>
  <p class="website">www.reedhomeworks.com</p>
</section>

<section class="card card--back">
  <svg class="card__art" viewBox="0 0 440 271" aria-hidden="true">
    <rect width="440" height="271" fill="var(--card-dark-back)"/>
    <use href="#house-shape"/>
    <g fill="var(--green)">
      <circle cx="56" cy="209" r="25"/><circle cx="121" cy="209" r="25"/><circle cx="187" cy="209" r="25"/>
      <circle cx="253" cy="209" r="25"/><circle cx="319" cy="209" r="25"/><circle cx="385" cy="209" r="25"/>
    </g>
    <g fill="#fff" stroke="#fff">
      <!-- mower -->
      <path d="M34 196 L48 210" stroke-width="2.5" fill="none"/>
      <path d="M46 208 H64 L72 214 V218 H44 Z" stroke="none"/>
      <circle cx="49" cy="220" r="3.5" stroke="none"/><circle cx="67" cy="220" r="3.5" stroke="none"/>
      <!-- trowel -->
      <path d="M102 213 H140" stroke-width="2" fill="none"/>
      <path d="M114 196 L128 192 L130 204 L118 208 Z" stroke="none"/>
      <path d="M122 207 V213" stroke-width="2"/>
      <!-- roller -->
      <rect x="178" y="194" width="17" height="9" rx="2" stroke="none"/>
      <path d="M195 198 H199 V207 H187 V213" fill="none" stroke-width="2"/>
      <rect x="184" y="213" width="6" height="12" rx="1" stroke="none"/>
      <!-- pressure washer -->
      <path d="M240 204 H262 M262 201 V207" stroke-width="3" fill="none"/>
      <path d="M244 204 L247 218 H252 L250 204" stroke="none"/>
      <path d="M265 200 L272 197 M265 204 H273 M265 208 L272 211" stroke-width="1.2"/>
      <!-- bin -->
      <path d="M307 198 H331 L328 220 H310 Z" stroke="none"/>
      <rect x="305" y="194" width="28" height="3" stroke="none"/>
      <circle cx="307" cy="220" r="4" stroke="none"/>
      <!-- window -->
      <rect x="373" y="197" width="24" height="24" stroke="none"/>
      <g fill="var(--green)" stroke="none">
        <rect x="376" y="200" width="8" height="8"/><rect x="386" y="200" width="8" height="8"/>
        <rect x="376" y="210" width="8" height="8"/><rect x="386" y="210" width="8" height="8"/>
      </g>
    </g>
  </svg>
  <ul class="services services--left">
    <li>Handyman</li><li>Landscaping</li><li>Sprinklers/Irrigation</li><li>Painting</li>
    <li>Electrical</li><li>Lighting</li><li>Power Washing</li><li>Hauling</li>
  </ul>
  <ul class="services services--right">
    <li>Cleaning</li><li>Bath/Kitchen</li><li>Baseboards/Trim/Moulding</li><li>Smart Home</li>
    <li>A/C and Heating</li><li>Blinds, Curtains</li><li>Assembly Services</li><li>Computer/Tech Service</li>
  </ul>
  <p class="website">www.reedhomeworks.com</p>
</section>

</body>
</html>
```